Beacon Advisory Website

I currently have a website www.beaconadvisoryinc.com. We are a IT Consulting Company. Our website will pretty much tell out our services. I am looking to enhance my website and make it look more professional. Looking for very classy and Contemporary look and design for my website.

It Company

```html
<!DOCTYPE html>
<html lang="en">
<head>
<meta charset="utf-8">
<title>Beacon Advisory</title>
<link href="https://fonts.googleapis.com/css2?family=Lato:wght@300;400;700;900&family=Fjalla+One&display=swap" rel="stylesheet">
<style>
:root{
  --blue:#0a6cb0;
  --blue-dark:#0b3f8c;
  --blue-light:#1d82c6;
  --ink:#2b2b2b;
  --footer:#222222;
  --panel:#141414;
  --white:#ffffff;
  --hero-a:#c4c4c4;
  --hero-b:#dcdcdc;
  --hero-c:#a9a9a9;
}
*{margin:0;padding:0;box-sizing:border-box}
html,body{width:1200px;height:1045px;overflow:hidden}
body{position:relative;font-family:'Lato',sans-serif;background:var(--white);color:var(--ink)}
.abs{position:absolute}

.topbar{left:0;top:0;width:1200px;height:33px;background:var(--blue)}
.topbar .phone{left:790px;top:7px;color:var(--white);font-weight:700;font-size:16px;display:flex;align-items:center;gap:8px}
.social-top{left:962px;top:0;display:flex;gap:1px}
.social-top span{width:34px;height:33px;background:var(--blue-light);display:block}

.header{left:0;top:33px;width:1200px;height:89px;background:var(--white)}
.brand{left:99px;top:27px;display:flex;align-items:center;gap:10px}
.brand .mark{width:38px;height:38px;border-radius:50%;background:var(--blue)}
.brand .name{font-weight:900;font-size:26px;color:var(--blue);letter-spacing:.5px}
.nav{left:460px;top:28px;display:flex;align-items:center}
.nav .home{width:34px;display:flex;justify-content:center;margin-right:4px}
.nav a{font-size:16px;font-weight:300;color:var(--ink);text-decoration:none;padding:0 10px;border-left:1px solid #ccc;line-height:20px;letter-spacing:.2px}

.hero{left:0;top:122px;width:1200px;height:636px;background:linear-gradient(135deg,var(--hero-a) 0%,var(--hero-b) 45%,var(--hero-c) 100%)}
.headline{left:99px;top:265px;font-family:'Fjalla One',sans-serif;font-weight:400;font-size:27px;line-height:36px;color:var(--white);text-shadow:0 2px 4px rgba(0,0,0,.45)}
.cta{left:99px;top:395px;width:249px;height:52px;background:var(--blue-dark);border:2px solid var(--white);color:var(--white);font-weight:900;font-size:20px;display:flex;align-items:center;justify-content:center;letter-spacing:-.3px}

.panel{top:530px;width:303px;height:180px;background:var(--panel);border-radius:3px;box-shadow:0 6px 12px rgba(0,0,0,.35)}
.panel .tab{position:absolute;left:-6px;top:7px;height:37px;background:var(--white);padding:0 32px 0 15px;display:flex;align-items:center;font-size:18px;color:var(--ink);clip-path:polygon(0 0,100% 0,calc(100% - 18px) 100%,0 100%);letter-spacing:.3px}
.panel .tab b{font-weight:400;color:var(--blue);margin-right:5px}
.panel .badge{position:absolute;left:18px;top:62px;width:78px;height:78px;border-radius:50%;background:var(--blue);border:2px solid var(--white);display:flex;align-items:center;justify-content:center}
.panel .body{position:absolute;left:113px;top:62px;right:18px;color:var(--white);font-size:12px;line-height:17px}
.panel .more{position:absolute;right:26px;bottom:11px;color:var(--white);font-size:12px;text-decoration:underline}
.services li{list-style:none;line-height:23px;font-size:12.5px}
.services li::before{content:">>";display:inline-block;width:20px;font-size:9px;letter-spacing:-1px}
.news .body{left:99px;top:64px;right:10px}
.news h4{font-family:Arial,sans-serif;font-size:12.5px;margin-bottom:5px;display:flex;gap:6px;align-items:center;white-space:nowrap}
.news p{font-family:Arial,sans-serif;font-size:11px;line-height:18px}

.footer{left:0;top:758px;width:1200px;height:243px;background:var(--footer);color:var(--white)}
.col h3{font-size:18px;font-weight:700;letter-spacing:.5px;padding-bottom:8px;border-bottom:1px dotted #555}
.links li{list-style:none;font-size:13.5px;line-height:23px}
.links li::before{content:">>";display:inline-block;width:25px;font-size:9px;letter-spacing:-1px;padding-left:2px}
.contact p{font-size:13.5px;line-height:18px}
.inquiry input,.inquiry textarea{display:block;width:216px;border:1px solid #ccc;background:var(--white);font-family:'Lato',sans-serif;font-size:12px;padding:4px 7px;margin-bottom:8px;color:#555}
.inquiry input{height:26px}
.inquiry textarea{height:44px;resize:none}
.inquiry button{background:var(--blue);color:var(--white);border:none;font-family:'Lato',sans-serif;font-weight:700;font-size:13px;padding:5px 11px;border-radius:2px}
.divider{top:50px;width:2px;height:145px;background:linear-gradient(#222,#3c3c3c,#222)}
.foot-brand{left:918px;top:58px;display:flex;align-items:center;gap:10px}
.foot-brand .mark{width:36px;height:36px;border-radius:50%;background:#8d8d8d}
.foot-brand .name{font-weight:900;font-size:23px;color:#a9a9a9}
.foot-social{left:937px;top:143px;display:flex;gap:7px}
.foot-social span{width:31px;height:31px;border-radius:50%;display:block}

.bottom{left:0;top:1001px;width:1200px;height:44px;background:var(--blue);color:var(--white);font-size:12px;display:flex;align-items:center;justify-content:center}
</style>
</head>
<body>

<div class="abs topbar">
  <div class="abs phone">
    <svg width="14" height="18" viewBox="0 0 14 18"><path d="M3 1 L6 4 L4 7 Q5 11 8 13 L10 11 L13 14 L11 17 Q3 15 1 4 Z" fill="#fff"/></svg>
    +1 (555) 014 2387
  </div>
  <div class="abs social-top" aria-label="Social links"><span></span><span></span><span></span><span></span></div>
</div>

<div class="abs header">
  <div class="abs brand"><span class="mark"></span><span class="name">BEACON ADVISORY</span></div>
  <nav class="abs nav">
    <span class="home"><svg width="22" height="20" viewBox="0 0 22 20"><path d="M11 1 L21 10 H18 V19 H13 V13 H9 V19 H4 V10 H1 Z" fill="var(--blue)"/></svg></span>
    <a>COMPANY</a><a>SERVICES</a><a>SOLUTIONS</a><a>RESOURCES</a><a>CAREER</a><a>CONTACT US</a>
  </nav>
</div>

<div class="abs hero" role="img" aria-label="Photo of a hand placing the last piece into a grey jigsaw puzzle"></div>

<h1 class="abs headline">We Will Delivers Highest Level Of Quality<br>Consultants And Services For The<br>Lowest Cost Of Ownership</h1>
<div class="abs cta">GET STARTED WITH US</div>

<section class="abs panel" style="left:99px">
  <div class="tab"><b>ABOUT</b>BEACON ADVISORY</div>
  <div class="badge"><svg width="40" height="40" viewBox="0 0 40 40"><ellipse cx="25" cy="12" rx="13" ry="9" fill="none" stroke="#fff" stroke-width="2"/><circle cx="14" cy="20" r="5" fill="#fff"/><path d="M4 36 Q4 26 14 26 Q24 26 24 36 Z" fill="#fff"/></svg></div>
  <div class="body">Today’s IT market is a dynamic, fast-paced industry, with ever-increasing demands. Meeting these demands for over 25 years, Beacon Advisory...</div>
  <a class="more">Read More</a>
</section>

<section class="abs panel" style="left:448px">
  <div class="tab"><b>OUR</b>SERVICES</div>
  <div class="badge"><svg width="40" height="40" viewBox="0 0 40 40"><g fill="#fff"><circle cx="20" cy="20" r="12"/><rect x="17" y="3" width="6" height="34"/><rect x="3" y="17" width="34" height="6"/><rect x="17" y="3" width="6" height="34" transform="rotate(45 20 20)"/><rect x="17" y="3" width="6" height="34" transform="rotate(-45 20 20)"/></g><circle cx="20" cy="20" r="5" fill="var(--blue)"/></svg></div>
  <ul class="body services" style="left:117px;top:61px">
    <li>Technology</li><li>Business</li><li>Application</li><li>Developement</li>
  </ul>
  <a class="more">Read More</a>
</section>

<section class="abs panel news" style="left:798px">
  <div class="tab"><b>INDUSTRIAL</b>NEWS</div>
  <div class="badge"><svg width="40" height="36" viewBox="0 0 40 36"><rect x="4" y="4" width="32" height="27" rx="4" fill="none" stroke="#fff" stroke-width="3"/><rect x="10" y="10" width="9" height="8" fill="#fff"/><rect x="22" y="10" width="9" height="3" fill="#fff"/><rect x="22" y="15" width="9" height="3" fill="#fff"/><rect x="10" y="21" width="21" height="3" fill="#fff"/></svg></div>
  <div class="body">
    <h4><svg width="12" height="10" viewBox="0 0 12 10"><path d="M1 5 L4.5 8.5 L11 1.5" fill="none" stroke="#fff" stroke-width="2.4"/></svg>Lorem ipsum dolor smit amet</h4>
    <p>consectetuer adipiscing litmk, sed amet diam nonummy nibh euismod tincidun nt ut reetml dolore aliq.</p>
  </div>
  <a class="more">Read More</a>
</section>

<footer class="abs footer">
  <div class="abs col" style="left:99px;top:26px;width:130px">
    <h3>Quick Links</h3>
    <ul class="links" style="margin-top:6px">
      <li>Home</li><li>Company</li><li>Services</li><li>Solutions</li><li>Resources</li><li>Career</li><li>Contact Us</li>
    </ul>
  </div>
  <div class="abs divider" style="left:266px"></div>

  <div class="abs col contact" style="left:317px;top:26px;width:194px">
    <h3>Contact Details</h3>
    <div style="display:flex;gap:8px;margin-top:14px">
      <svg width="10" height="14" viewBox="0 0 10 14"><path d="M5 0 A5 5 0 0 1 10 5 Q10 8 5 14 Q0 8 0 5 A5 5 0 0 1 5 0Z" fill="#fff"/><circle cx="5" cy="5" r="2" fill="var(--footer)"/></svg>
      <p><b>HEAD OFFICE</b><br>48 Harbor Lane<br>Suite 310<br>Westbrook, NJ 07999</p>
    </div>
    <div style="display:flex;gap:9px;margin-top:15px;align-items:center">
      <svg width="12" height="14" viewBox="0 0 14 18"><path d="M3 1 L6 4 L4 7 Q5 11 8 13 L10 11 L13 14 L11 17 Q3 15 1 4 Z" fill="#fff"/></svg>
      <p><b>+1 (555) 014 2387</b></p>
    </div>
    <div style="display:flex;gap:9px;margin-top:17px;align-items:center">
      <svg width="14" height="10" viewBox="0 0 14 10"><rect x=".5" y=".5" width="13" height="9" fill="none" stroke="#fff"/><path d="M.5 .5 L7 6 L13.5 .5" fill="none" stroke="#fff"/></svg>
      <p>info@beaconadvisory.com</p>
    </div>
  </div>
  <div class="abs divider" style="left:550px"></div>

  <div class="abs col inquiry" style="left:601px;top:26px;width:228px">
    <h3>Quick Inquiry</h3>
    <div style="margin-top:16px">
      <input placeholder="Name">
      <input placeholder="Email">
      <textarea placeholder="Message"></textarea>
      <button>Submit</button>
    </div>
  </div>
  <div class="abs divider" style="left:868px"></div>

  <div class="abs foot-brand"><span class="mark"></span><span class="name">BEACON</span></div>
  <div class="abs foot-social" aria-label="Social links">
    <span style="background:#3b5998"></span><span style="background:#1da1f2"></span><span style="background:#e0262b"></span><span style="background:#dd4b39"></span>
  </div>
</footer>

<div class="abs bottom">Copyright © 2016 Beacon Advisory Inc.&nbsp; All Rights Reserved.</div>

</body>
</html>
```